BUSINESS CARD - HALLORAN FIELD SERVICES

I would like to create a business card for my fertilizer spreading business. I would like to incorporate my existing logo and also a description of the services offered. The business card will be given to farmers so must be kept simple but effective. It will also be left in stores so much also be eye catching in order to stand out from other cards.

Target Market(s)

FARMERS

Requirements
Must have
• FRONT OF CARD = EXISTING LOGO + "CUSTOMISED SPREADING" below the logo

REAR Of CARD = SERVICES OFFERED AND CONTACT DETAILS

- Bulk fertilizer including Lime, Gypsum, Manure & Compost
- Granular fertilizer including Single Super, Urea, Gran-am, & Custom Blends
- Modern equipment - Autosteer & Variable Rate Capable
- Friendly & Reliable Service
- Contact Gus: 0417 552 308
Nice to have
• utilize same color scheme as existing logo

```html
<!DOCTYPE html>
<html lang="en">
<head>
<meta charset="utf-8">
<title>Halloran Field Services – Business Card</title>
<link rel="stylesheet" href="https://fonts.googleapis.com/css2?family=Poppins:wght@400;500;600;700&display=swap">
<style>
  :root {
    --backdrop: #2b2e33;
    --card: #ffffff;
    --orange: #f28c1e;
    --wheat: #f5a53c;
    --charcoal: #4a4a4c;
    --ink: #2f2f31;
  }
  * { box-sizing: border-box; margin: 0; padding: 0; }
  html, body { width: 1200px; height: 900px; overflow: hidden; }
  body {
    background: var(--backdrop);
    font-family: "Poppins", sans-serif;
    display: flex;
    align-items: center;
    justify-content: center;
    gap: 50px;
  }
  .card {
    position: relative;
    width: 540px;
    height: 310px;
    background: var(--card);
    border-radius: 4px;
    overflow: hidden;
    box-shadow: 0 10px 30px rgba(0,0,0,.35);
  }

  /* shared brand lockup */
  .brand {
    position: absolute;
    display: flex;
    align-items: center;
    gap: 12px;
  }
  .brand-dot {
    width: 58px; height: 58px;
    border-radius: 50%;
    background: var(--charcoal);
    flex: none;
  }
  .brand-name {
    font-weight: 600;
    font-size: 21px;
    line-height: 1.1;
    color: var(--charcoal);
    letter-spacing: -.2px;
  }

  /* rear: services */
  .services { position: absolute; left: 28px; top: 22px; width: 280px; }
  .services-title {
    font-weight: 700;
    font-size: 22px;
    color: var(--charcoal);
    padding-bottom: 4px;
    border-bottom: 2px solid var(--orange);
    display: inline-block;
    margin-bottom: 10px;
  }
  .services-list { list-style: none; }
  .services-list li {
    position: relative;
    padding-left: 12px;
    font-size: 12px;
    line-height: 1.35;
    color: var(--ink);
    margin-bottom: 4px;
  }
  .services-list li::before {
    content: "";
    position: absolute;
    left: 0; top: 6px;
    width: 5px; height: 5px;
    border-radius: 50%;
    background: var(--orange);
  }
  .rear .brand { right: 24px; top: 148px; }
  .rear .brand-name { font-size: 18px; }
  .rear .brand-dot { width: 50px; height: 50px; }

  .footer-bands { position: absolute; left: 0; bottom: 0; width: 540px; height: 90px; }
  .contact {
    position: absolute;
    left: 16px; bottom: 60px;
    display: flex; align-items: center; gap: 7px;
    font-size: 11px; color: #fff;
  }
  .contact svg { width: 12px; height: 12px; }
  .tagline {
    position: absolute;
    right: 26px; bottom: 16px;
    font-weight: 600;
    font-size: 19px;
    line-height: 1.2;
    color: #fff;
  }

  /* front: logo */
  .wheat {
    position: absolute;
    left: 0; top: 0;
    width: 230px; height: 160px;
    background: radial-gradient(ellipse at 35% 40%, var(--wheat) 0%, rgba(245,165,60,.55) 55%, rgba(245,165,60,0) 75%);
  }
  .front .brand { left: 210px; top: 125px; }
  .front .brand-name { border-bottom: 2px solid var(--orange); padding-bottom: 4px; }
  .front-tagline {
    position: absolute;
    left: 280px; top: 200px;
    font-weight: 500;
    font-size: 13px;
    letter-spacing: 3px;
    color: var(--orange);
  }
</style>
</head>
<body>

  <section class="card rear" aria-label="Rear of card">
    <div class="services">
      <h2 class="services-title">Services Offered</h2>
      <ul class="services-list">
        <li>Bulk fertilizer including Lime, Gypsum, Manure &amp; Compost</li>
        <li>Granular fertilizer including Single Super, Urea, Gran-am, &amp; Custom Blends</li>
        <li>Modern equipment - Autosteer &amp; Variable Rate Capable</li>
      </ul>
    </div>

    <div class="brand">
      <span class="brand-dot"></span>
      <span class="brand-name">Halloran Field<br>Services</span>
    </div>

    <svg class="footer-bands" viewBox="0 0 540 90" preserveAspectRatio="none" aria-hidden="true">
      <rect x="0" y="0" width="300" height="44" fill="var(--charcoal)"/>
      <path d="M0 40 H215 C250 40 255 6 295 6 H540 V90 H0 Z" fill="var(--orange)"/>
    </svg>
    <div class="contact">
      <svg viewBox="0 0 24 24" aria-hidden="true"><circle cx="12" cy="12" r="12" fill="#fff"/><path d="M8 6l2 0 1 3-1.5 1a7 7 0 0 0 3.5 3.5L14 12l3 1 0 2c0 1-1 2-2 2A10 10 0 0 1 7 8c0-1 0-2 1-2z" fill="var(--charcoal)"/></svg>
      <span>0417 552 308</span>
    </div>
    <p class="tagline">Friendly &amp; Reliable Service</p>
  </section>

  <section class="card front" aria-label="Front of card">
    <div class="wheat" role="img" aria-label="Decorative orange wheat ears sweeping in from the top left corner"></div>
    <div class="brand">
      <span class="brand-dot"></span>
      <span class="brand-name">Halloran Field<br>Services</span>
    </div>
    <p class="front-tagline">CUSTOMISED SPREADING</p>
  </section>

</body>
</html>
```